Best local air conditioning and heating contractor

We need a website design for a new company in Tampa Bay called the Coastal Breeze Cooling Company. We provide superior services for residential and commercial properties as well as maintenance and installing HVAC systems. We also want to sell equipment, parts and filter on the website as well. We want it easy to use for customers. Rich with content and keywords for our area.

Target Market(s)

homeowners in Tampa Bay

Industry/Entity Type

HVAC air conditioning and heating

Coding

Coded - Design and coding required

Number of Pages Required

5+ page

Font styles to use
Sans Serif

Requirements
Nice to have
• would like the colors to be same as logo

```html
<!DOCTYPE html>
<html lang="en">
<head>
<meta charset="utf-8">
<title>Coastal Breeze Cooling Company – Our Services</title>
<link href="https://fonts.googleapis.com/css2?family=Syncopate:wght@700&family=Outfit:wght@300;400;500;600&display=swap" rel="stylesheet">
<style>
:root{
  --navy:#2b3a78;
  --navy-dark:#24306a;
  --red:#dc2127;
  --ink:#111;
  --body:#444;
  --white:#fff;
}
*{box-sizing:border-box;margin:0;padding:0}
html,body{width:1200px;height:3054px;overflow:hidden;background:var(--white)}
body{position:relative;font-family:"Outfit",sans-serif;color:var(--body)}
.abs{position:absolute}

/* top bar */
.topbar{left:0;top:0;width:1200px;height:28px;background:var(--navy);color:var(--white);font-size:12px;font-weight:500}
.topbar .item{position:absolute;top:7px;white-space:nowrap}
.stars{color:#f3c623;letter-spacing:1px}
.topbar .sep{position:absolute;top:4px;width:1px;height:20px;background:rgba(255,255,255,.35)}
.topbar .soc{position:absolute;top:8px;width:11px;height:11px;border-radius:2px;background:var(--white)}

/* header */
.header{left:0;top:28px;width:1200px;height:77px;background:var(--white)}
.brand{position:absolute;left:101px;top:20px;display:flex;align-items:center;gap:8px;font-weight:600;font-size:15px;color:var(--navy);line-height:1.1;width:170px}
.brand .dot{width:14px;height:14px;background:var(--red);border-radius:50%;flex:none}
.nav{position:absolute;left:375px;top:32px;display:flex;gap:29px;font-size:15px;font-weight:500;color:var(--ink)}
.call{position:absolute;left:887px;top:0;width:313px;height:77px;background:var(--red);color:var(--white)}
.call .small{position:absolute;left:48px;top:12px;font-size:17px}
.call .num{position:absolute;left:48px;top:32px;font-size:31px;font-weight:600;letter-spacing:.5px}
.phone-badge{position:absolute;left:873px;top:43px;width:50px;height:50px;border-radius:50%;background:var(--navy);border:4px solid #f2c9cb}

/* hero */
.hero{left:0;top:105px;width:1200px;height:312px;background:linear-gradient(90deg,#3c3f4a 0%,#4a4e5c 45%,#8a3a42 75%,#c2464c 100%)}
.hero h1{position:absolute;left:0;right:0;top:158px;text-align:center;font-family:"Syncopate",sans-serif;font-size:34px;color:var(--white);letter-spacing:1px}

/* service rows */
.frame-red{background:var(--red)}
.photo{background:linear-gradient(135deg,#d9dde6,#9aa3b5)}
.icon-badge{width:78px;height:78px;border-radius:50%;background:var(--navy);border:5px solid #e8868a;display:flex;align-items:center;justify-content:center}
.svc-title{font-family:"Syncopate",sans-serif;font-size:35px;line-height:38px;color:var(--ink);white-space:nowrap}
.svc-title .hl{color:var(--red)}
.underline{width:85px;height:4px;background:var(--red)}
.svc-text{font-size:14.6px;line-height:25.6px;text-align:justify;color:var(--body)}

/* emergency */
.emergency{left:0;top:2142px;width:1200px;height:560px;background:linear-gradient(90deg,#b8bdb4 0%,#8d5049 30%,#7a3a33 70%,#6d2f2a 100%)}
.emg-panel{left:186px;top:2236px;width:826px;height:466px;background:rgba(255,255,255,.92);border-top:3px solid var(--red)}
.emg-panel h2{position:absolute;left:0;right:0;top:46px;text-align:center;font-family:"Syncopate",sans-serif;font-size:36px;color:var(--ink)}
.emg-panel h2 .hl{color:var(--red)}
.emg-line{position:absolute;left:384px;top:101px;width:72px;height:3px;background:var(--red)}
.emg-panel h3{position:absolute;left:0;right:0;top:125px;text-align:center;font-size:17px;font-weight:600;color:var(--ink)}
.emg-intro{position:absolute;left:54px;width:718px;top:159px;text-align:center;font-size:14.6px;line-height:25.6px;color:#333}
.emg-list{position:absolute;left:33px;top:284px;list-style:none;font-size:14.6px;line-height:25.6px;color:#333}
.emg-rule{left:0;top:2702px;width:1200px;height:6px;background:var(--red)}

/* footer */
.footer{left:0;top:2708px;width:1200px;height:346px;background:var(--navy);color:var(--white)}
.f-brand{position:absolute;left:104px;top:62px;display:flex;align-items:center;gap:10px;font-size:22px;font-weight:600;line-height:1.15;width:270px}
.f-brand .sq{width:18px;height:18px;background:var(--white);flex:none}
.f-soc{position:absolute;top:189px;width:38px;height:38px;border-radius:50%;background:var(--white)}
.f-col{position:absolute;top:58px}
.f-col h4{font-size:17px;font-weight:600;color:#8fc7ff;margin-bottom:10px}
.f-col li{list-style:none;font-size:13.5px;line-height:30.5px}
.f-divider{left:100px;top:2998px;width:1000px;height:1px;background:rgba(255,255,255,.35)}
.copyright{left:0;right:0;top:3018px;text-align:center;font-size:15px;color:var(--white)}
</style>
</head>
<body>

<!-- top bar -->
<div class="abs topbar">
  <span class="item" style="left:101px"><span class="stars">★★★★★</span> 4.8 STAR SERVICES (20REVIEWS)</span>
  <span class="sep" style="left:366px"></span>
  <span class="item" style="left:374px">
    <svg width="10" height="10" viewBox="0 0 10 10"><circle cx="5" cy="5" r="4" fill="none" stroke="#dc2127" stroke-width="1.5"/><path d="M5 3v2.2l1.3 1" stroke="#dc2127" stroke-width="1.2" fill="none"/></svg>
    Mon to Fri 9:00 am to 6:00 pm</span>
  <span class="item" style="left:803px">
    <svg width="8" height="11" viewBox="0 0 8 11"><path d="M4 0a4 4 0 0 1 4 4c0 3-4 7-4 7S0 7 0 4a4 4 0 0 1 4-4z" fill="#dc2127"/></svg>
    Serving The Tampa Bay Area</span>
  <span class="sep" style="left:980px"></span>
  <span class="soc" style="left:992px"></span>
  <span class="sep" style="left:1011px"></span>
  <span class="soc" style="left:1021px"></span>
  <span class="sep" style="left:1041px"></span>
  <span class="soc" style="left:1053px"></span>
  <span class="sep" style="left:1080px"></span>
  <span class="soc" style="left:1087px"></span>
</div>

<!-- header -->
<header class="abs header">
  <div class="brand"><span class="dot"></span>Coastal Breeze Cooling Company</div>
  <nav class="nav"><span>ABOUT US</span><span>SERVICES</span><span>HVAC</span><span>RESOURCES</span><span>CONTACT</span></nav>
  <div class="call">
    <div class="small">Call Today for Service</div>
    <div class="num">727 - 555 - 0192</div>
  </div>
</header>
<div class="abs phone-badge">
  <svg width="42" height="42" viewBox="0 0 42 42"><path d="M15 12c1-1 2-1 3 0l2 3c.6 1 .3 2-.5 2.6l-1.2 1c1 2.5 3 4.5 5.5 5.5l1-1.2c.6-.8 1.6-1.1 2.6-.5l3 2c1 1 1 2 0 3l-1.5 1.5c-1.5 1.5-5 1-9-3s-4.5-7.5-3-9z" fill="#fff"/></svg>
</div>

<!-- hero -->
<section class="abs hero" role="img" aria-label="Outdoor air conditioning condenser unit beside a house wall with a red tint">
  <h1>OUR SERVICES</h1>
</section>

<!-- AC Repair -->
<div class="abs frame-red" style="left:101px;top:491px;width:467px;height:460px"></div>
<div class="abs photo" style="left:113px;top:504px;width:466px;height:458px" role="img" aria-label="Technician repairing a wall-mounted split air conditioner with a screwdriver"></div>
<div class="abs icon-badge" style="left:643px;top:520px">
  <svg width="38" height="38" viewBox="0 0 38 38" fill="none" stroke="#fff" stroke-width="2" stroke-linecap="round"><path d="M7 31L24 14"/><circle cx="27" cy="11" r="5"/><path d="M7 7l24 24"/><path d="M5 9l4-4 3 3-4 4z"/></svg>
</div>
<h2 class="abs svc-title" style="left:643px;top:610px">AC <span class="hl">REPAIR</span></h2>
<div class="abs underline" style="left:643px;top:652px"></div>
<p class="abs svc-text" style="left:643px;top:676px;width:455px">Sed ut perspiciatis unde omnis iste natus error sit voluptatem accusantium doloremque laudantium, totam rem aperiam, eaque ipsa quae ab illo inventore veritatis et quasi architecto beatae vitae dicta sunt explicabo. Nemo enim ipsam voluptatem quia voluptas sit aspernatur aut odit aut fugit, sed quia consequuntur magni dolores eos qui ratione voluptatem sequi nesciunt. Neque porro quisquam est, qui dolorem ipsum quia dolor sit amet,<br>consectetur, adipisci velit, sed quia non numquam eius modi tempora incidunt ut labore et dolore magnam aliquam quaerat voluptatem. Ut enim ad minima veniam, quis nostrum</p>

<!-- AC Installation -->
<div class="abs icon-badge" style="left:100px;top:1063px">
  <svg width="38" height="38" viewBox="0 0 38 38" fill="none" stroke="#fff" stroke-width="2"><rect x="5" y="7" width="26" height="18" rx="2"/><path d="M9 13h14M9 18h10"/><path d="M22 22l8 8" stroke-linecap="round"/></svg>
</div>
<h2 class="abs svc-title" style="left:100px;top:1153px">AC <span class="hl">INSTALLATION</span></h2>
<div class="abs underline" style="left:100px;top:1195px"></div>
<p class="abs svc-text" style="left:100px;top:1219px;width:456px">Sed ut perspiciatis unde omnis iste natus error sit voluptatem accusantium doloremque laudantium, totam rem aperiam, eaque ipsa quae ab illo inventore veritatis et quasi architecto beatae vitae dicta sunt explicabo. Nemo enim ipsam voluptatem quia voluptas sit aspernatur aut odit aut fugit, sed quia consequuntur magni dolores eos qui ratione voluptatem sequi nesciunt. Neque porro quisquam est, qui dolorem ipsum quia dolor sit amet,<br>consectetur, adipisci velit, sed quia non numquam eius modi tempora incidunt ut labore et dolore magnam aliquam quaerat voluptatem. Ut enim ad minima veniam, quis nostrum</p>
<div class="abs frame-red" style="left:631px;top:1035px;width:467px;height:460px"></div>
<div class="abs photo" style="left:620px;top:1046px;width:466px;height:459px;background:linear-gradient(135deg,#9a4d3a,#6f7b8c 60%,#c9ccd2)" role="img" aria-label="Two technicians installing an outdoor condenser unit beside a brick wall"></div>

<!-- HVAC Maintenance -->
<div class="abs frame-red" style="left:101px;top:1577px;width:467px;height:460px"></div>
<div class="abs photo" style="left:113px;top:1589px;width:466px;height:458px;background:linear-gradient(135deg,#e2e6ec,#8fa9c8 55%,#d8703a)" role="img" aria-label="Technician in hard hat and safety vest inspecting rooftop HVAC units with a tablet"></div>
<div class="abs icon-badge" style="left:643px;top:1592px">
  <svg width="38" height="38" viewBox="0 0 38 38" fill="none" stroke="#fff" stroke-width="2"><rect x="5" y="8" width="28" height="22" rx="2"/><circle cx="21" cy="19" r="6"/><path d="M9 13h5M9 18h5M9 23h5"/></svg>
</div>
<h2 class="abs svc-title" style="left:643px;top:1683px">HVAC<br><span class="hl">MAINTENANCE</span></h2>
<div class="abs underline" style="left:643px;top:1760px"></div>
<p class="abs svc-text" style="left:643px;top:1782px;width:455px">Sed ut perspiciatis unde omnis iste natus error sit voluptatem accusantium doloremque laudantium, totam rem aperiam, eaque ipsa quae ab illo inventore veritatis et quasi architecto beatae vitae dicta sunt explicabo. Nemo enim ipsam voluptatem quia voluptas sit aspernatur aut odit aut fugit, sed quia consequuntur magni dolores eos qui ratione voluptatem sequi nesciunt. Neque porro quisquam est, qui dolorem ipsum quia dolor sit amet,<br>consectetur, adipisci velit, sed quia non numquam eius modi tempora incidunt ut labore et dolore magnam aliquam quaerat voluptatem. Ut enim ad minima veniam, quis nostrum</p>

<!-- Emergency -->
<section class="abs emergency" role="img" aria-label="Air conditioning unit on grass beside a red brick house wall"></section>
<div class="abs emg-panel">
  <h2>EMERGENCY <span class="hl">SERVICES</span></h2>
  <div class="emg-line"></div>
  <h3>What Is an Emergency Situation?</h3>
  <p class="emg-intro">An emergency situation is a situation that requires immediate attention! This can include a situation where your HVAC system is not working properly, or there is a lack of airflow. If you notice that your HVAC system is not working properly, it is important to not wait to call for help. An emergency situation can quickly become more serious if it is not addressed in a timely manner.<br>Examples of emergency situations include:</p>
  <ul class="emg-list">
    <li>Lack of airflow</li>
    <li>Extremely high temperatures in your home</li>
    <li>Burning or electrical smells coming from your HVAC system</li>
    <li>Lack of cooling</li>
    <li>Abnormal noises coming from your HVAC system</li>
    <li>Water leaking from your HVAC system ac installation service ductless heating and cooling air conditioning installation</li>
  </ul>
</div>
<div class="abs emg-rule"></div>

<!-- footer -->
<footer class="abs footer">
  <div class="f-brand"><span class="sq"></span>Coastal Breeze Cooling Company</div>
  <span class="f-soc" style="left:130px"></span>
  <span class="f-soc" style="left:183px"></span>
  <span class="f-soc" style="left:236px"></span>
  <span class="f-soc" style="left:288px"></span>
  <div class="f-col" style="left:466px"><h4>Quick Links</h4><ul><li>Home</li><li>About Us</li><li>Services</li><li>Hvac</li><li>Resources</li><li>Contact</li></ul></div>
  <div class="f-col" style="left:653px"><h4>Our Services</h4><ul><li>AC Repair</li><li>AC Installation</li><li>HVAC Maintenance</li><li>Duct Services</li></ul></div>
  <div class="f-col" style="left:866px"><h4>Contact Info</h4><ul><li>Tampa, Florida, United States</li><li>727-555-0192</li><li>hello@coastalbreezecooling.com</li></ul></div>
</footer>
<div class="abs f-divider"></div>
<div class="abs copyright">©Copyright 2024 The Coastal Breeze Cooling Company. All Rights Reserved.</div>

</body>
</html>
```